holloway paving service

Needs to have phone number 0418259730 and email markholloway@brightmail.com.au.
ABN 62318470915
name mark holloway

For all your concreting solutions
Excavation
Exposed & colour concrete
House & shed slabs
Driveways
Landing & steps

Contact Information for Business Card

ph 0418259730
email markholloway@brightmail.com.au.
ABN 62318470915
name mark holloway

```html
<!DOCTYPE html>
<html lang="en">
<head>
<meta charset="utf-8">
<title>Holloway Paving Service — Business Card</title>
<link rel="stylesheet" href="https://fonts.googleapis.com/css2?family=Montserrat:wght@600;700&family=Lato:wght@400&display=swap">
<style>
  :root {
    --page-bg: #e9e7e4;
    --brand-orange: #f26a21;
    --brand-grey: #636363;
    --diamond-light: #f7f7f7;
    --diamond-mid: #e4e4e4;
    --ink-dark: #5a5a5a;
    --ink-white: #ffffff;
  }
  html, body {
    margin: 0;
    padding: 0;
    width: 1200px;
    height: 900px;
    overflow: hidden;
    background: var(--page-bg);
  }
  .business-card {
    position: absolute;
    left: 120px;
    top: 153px;
    width: 960px;
    height: 593px;
    overflow: hidden;
    box-shadow: 0 10px 30px rgba(0,0,0,0.18);
  }
  .card-shapes {
    position: absolute;
    inset: 0;
  }
  .contact-block,
  .services-block {
    position: absolute;
    left: 35px;
    margin: 0;
    color: var(--ink-white);
  }
  .holder-name {
    position: absolute;
    left: 35px;
    top: 78px;
    margin: 0;
    font-family: "Montserrat", sans-serif;
    font-weight: 700;
    font-size: 32px;
    letter-spacing: 0.5px;
    color: var(--ink-white);
  }
  .contact-block {
    top: 134px;
    font-family: "Lato", sans-serif;
    font-size: 25px;
    line-height: 35px;
  }
  .contact-block .abn { margin-bottom: 17px; }
  .services-heading {
    position: absolute;
    left: 35px;
    top: 307px;
    margin: 0;
    font-family: "Montserrat", sans-serif;
    font-weight: 700;
    font-size: 26px;
    line-height: 35px;
    color: var(--ink-white);
  }
  .services-block {
    top: 385px;
    padding: 0;
    list-style: none;
    font-family: "Lato", sans-serif;
    font-size: 25px;
    line-height: 35px;
  }
  .services-block li::before {
    content: "";
    display: inline-block;
    width: 9px;
    height: 9px;
    margin: 0 12px 4px 3px;
    background: var(--ink-white);
    transform: rotate(45deg);
  }
  .brand-lockup {
    position: absolute;
    left: 465px;
    top: 200px;
    width: 400px;
    text-align: center;
    font-family: "Montserrat", sans-serif;
    font-weight: 700;
    font-size: 34px;
    line-height: 44px;
    letter-spacing: 1px;
    color: var(--ink-dark);
  }
  .brand-lockup .brand-square {
    display: block;
    width: 40px;
    height: 40px;
    margin: 0 auto 18px;
    background: var(--brand-orange);
  }
  .brand-lockup .brand-name { margin: 0; }
</style>
</head>
<body>
  <article class="business-card">
    <svg class="card-shapes" width="960" height="593" viewBox="0 0 960 593" aria-hidden="true">
      <defs>
        <linearGradient id="diamond-fill" x1="0" y1="0" x2="1" y2="1">
          <stop offset="0" stop-color="var(--diamond-light)"/>
          <stop offset="1" stop-color="var(--diamond-mid)"/>
        </linearGradient>
      </defs>
      <rect class="panel-orange" x="0" y="0" width="665" height="593" fill="var(--brand-orange)"/>
      <rect class="panel-grey" x="665" y="0" width="295" height="593" fill="var(--brand-grey)"/>
      <polygon class="brand-diamond" points="665,17 942,294 665,571 388,294" fill="url(#diamond-fill)" opacity="0.96"/>
    </svg>

    <h1 class="holder-name">MARK HOLLOWAY</h1>
    <div class="contact-block">
      <div class="abn">ABN 62318470915</div>
      <div class="phone">0418259730</div>
      <div class="email">markholloway@brightmail.com.au</div>
    </div>

    <h2 class="services-heading">FOR ALL YOUR<br>CONCRETING SOLUTIONS</h2>
    <ul class="services-block">
      <li>Excavation</li>
      <li>Exposed &amp; colour concrete</li>
      <li>House &amp; shed slabs</li>
      <li>Driveways</li>
      <li>Landing &amp; steps</li>
    </ul>

    <div class="brand-lockup">
      <span class="brand-square"></span>
      <p class="brand-name">HOLLOWAY PAVING<br>SERVICE</p>
    </div>
  </article>
</body>
</html>
```